NZ First of it's kind solutions directory and marketplace for busy Mums needs a business card design

We need a business card design for our new nationwide business in NZ (long term plans to go global). We provide solutions to the everyday challenges that busy Mums face by connecting them with quality communities and suppliers of carefully selected, relevant products and services. We sell direct via our online marketplace. The final design should communicate our values of inclusivity, quality and smart solutions. Colours should incorporate our logo colour palette of #477077 and #6ba8b2. Our website is at https://www.brightnestmums.example

Target Market(s)

busy Mums, Age 28 – 50, female, income over $100K, location main centres NZ primarily but NZ wide. Is likely juggling work or career with a young family. Probably had hobbies which have fallen by the wayside.
-Wants to succeed in her chosen career without compromising on family life
-to successfully juggle her career without feeling like she is compromising her children
- Is time poor, something always has to give and it’s generally her health (she’ll stay up late, get stressed)
- probably ex corporate or professional career. Has discretional income

Industry/Entity Type

Business

Contact Information for Business Card

Lena Forbisher, Founder, BrightNestMums.example (Strapline Tap; Gather; Sorted), 47 Kowhai Terrace, Ellerslie, Auckland 1051, New Zealand. Mob: 021 483 517 Ph: +64 (0)9 571 4860

Font styles to use
Other font styles liked:
• Raleway, and/or Architects Daughter

Colors
00a990
33b8a4
86cfc6
cfeae6

Requirements
Must have
• the above details, streamline. the logo and colours associated with those logos
Should not have
• foil or metallic colours

```html
<!DOCTYPE html>
<html lang="en">
<head>
<meta charset="utf-8">
<title>BrightNestMums – Business Card</title>
<link rel="stylesheet" href="https://fonts.googleapis.com/css2?family=Nunito:wght@800&family=Roboto+Condensed:ital,wght@0,400;1,400&display=swap">
<style>
  :root {
    --brand-dark: #477077;
    --brand-deep: #3b5d63;
    --brand-light: #6ba8b2;
    --ink: #3a3a3a;
    --card: #f6f6f6;
    --backdrop: #e6e6e6;
  }
  * { box-sizing: border-box; margin: 0; padding: 0; }
  html, body {
    width: 1200px; height: 576px; overflow: hidden;
    background: var(--backdrop);
  }
  .canvas { position: relative; width: 1200px; height: 576px; }

  .card {
    position: absolute;
    width: 484px; height: 292px;
    background: var(--card);
    border-radius: 14px;
    overflow: hidden;
    box-shadow: 0 2px 6px rgba(0,0,0,0.12);
  }
  .card--front { left: 82px; top: 139px; }
  .card--back  { left: 602px; top: 139px; }

  .wordmark {
    font-family: "Nunito", sans-serif;
    font-weight: 800;
    color: var(--brand-dark);
    white-space: nowrap;
    letter-spacing: -0.5px;
  }
  .brand-dot {
    display: inline-block;
    flex: none;
    border-radius: 50%;
    background: var(--brand-dark);
  }

  /* Front */
  .front-lockup {
    position: absolute; left: 0; right: 0; top: 160px;
    display: flex; align-items: center; justify-content: center; gap: 10px;
  }
  .front-lockup .brand-dot { width: 26px; height: 26px; }
  .front-lockup .wordmark { font-size: 34px; line-height: 40px; }
  .strapline {
    position: absolute; left: 0; right: 0; top: 206px;
    text-align: center;
    font-family: "Roboto Condensed", sans-serif;
    font-size: 11px; line-height: 14px; letter-spacing: 4px;
    color: var(--ink);
  }
  .strapline .divider { color: var(--brand-light); margin: 0 8px; }

  /* Back */
  .back-lockup {
    position: absolute; left: 32px; top: 60px;
    display: flex; align-items: center; gap: 10px;
  }
  .back-lockup .brand-dot { width: 26px; height: 26px; }
  .back-lockup .wordmark { font-size: 34px; line-height: 40px; }

  .person { position: absolute; left: 36px; top: 212px; }
  .person__name {
    font-family: "Nunito", sans-serif; font-weight: 800;
    font-size: 20px; line-height: 24px; color: var(--brand-deep);
  }
  .person__role {
    font-family: "Roboto Condensed", sans-serif;
    font-style: italic; font-size: 13px; line-height: 16px; color: var(--ink);
  }

  .contact {
    position: absolute; left: 269px; top: 136px;
    font-family: "Roboto Condensed", sans-serif;
    font-size: 13px; color: var(--ink); line-height: 18px;
  }
  .contact__address { margin-bottom: 9px; }
  .contact__line { display: flex; align-items: center; gap: 8px; height: 19px; }
  .contact__icon { width: 11px; height: 11px; fill: var(--brand-light); flex: none; }

  .band-strip {
    position: absolute; left: 0; bottom: 0; width: 100%; height: 10px;
    background: var(--brand-light);
  }
  .band-panel {
    position: absolute; right: 0; bottom: 0; width: 264px; height: 36px;
    background: var(--brand-deep);
    clip-path: polygon(18px 0, 100% 0, 100% 100%, 0 100%);
    display: flex; align-items: center; padding-left: 49px;
    font-family: "Roboto Condensed", sans-serif; font-size: 13px; color: #fff;
  }
</style>
</head>
<body>
<main class="canvas">

  <section class="card card--front" aria-label="Card front">
    <div class="front-lockup">
      <span class="brand-dot" aria-hidden="true"></span>
      <span class="wordmark">BrightNestMums</span>
    </div>
    <p class="strapline">TAP<span class="divider">|</span>GATHER<span class="divider">|</span>SORTED</p>
  </section>

  <section class="card card--back" aria-label="Card back">
    <div class="back-lockup">
      <span class="brand-dot" aria-hidden="true"></span>
      <span class="wordmark">BrightNestMums</span>
    </div>

    <div class="contact">
      <p class="contact__address">47 Kowhai Terrace, Ellerslie,<br>Auckland 1051, New Zealand</p>
      <p class="contact__line">
        <svg class="contact__icon" viewBox="0 0 12 12" aria-hidden="true"><path d="M3 0h6a1 1 0 0 1 1 1v10a1 1 0 0 1-1 1H3a1 1 0 0 1-1-1V1a1 1 0 0 1 1-1zm0 2v7h6V2zm3 8a.7.7 0 1 0 0 1.4A.7.7 0 0 0 6 10z"/></svg>
        021 483 517
      </p>
      <p class="contact__line">
        <svg class="contact__icon" viewBox="0 0 12 12" aria-hidden="true"><path d="M1 3c0-1 1-2 5-2s5 1 5 2v1H8.5V3h-5v1H1zm2 2h6l2 3v3H1V8zm3 1.2a1.5 1.5 0 1 0 0 3 1.5 1.5 0 0 0 0-3z"/></svg>
        +64 (0)9 571 4860
      </p>
      <p class="contact__line">
        <svg class="contact__icon" viewBox="0 0 12 12" aria-hidden="true"><path d="M0 2h12v8H0zm1 1v.4l5 3.2 5-3.2V3zm0 1.6V9h10V4.6L6 7.8z"/></svg>
        lena@brightnestmums.example
      </p>
    </div>

    <div class="person">
      <p class="person__name">Lena Forbisher</p>
      <p class="person__role">Founder</p>
    </div>

    <div class="band-strip" aria-hidden="true"></div>
    <div class="band-panel">www.BrightNestMums.example</div>
  </section>

</main>
</body>
</html>
```